Fernhale Business Card Design

We are looking for a fresh business card design for our new logo. We would like a business card that is unique but friendly. We are in the window coverings business offering blinds, shutters and shades for homes.

Target Market(s)

Targeting the end-consumer

Industry/Entity Type

Business

Requirements
Must have
• Must have a dedicates space for a photo of our sales person. Must contain our new logo (attached).

```html
<!DOCTYPE html>
<html lang="en">
<head>
<meta charset="utf-8">
<title>Fernhale Business Card</title>
<link href="https://fonts.googleapis.com/css2?family=Lato:wght@400;700&display=swap" rel="stylesheet">
<style>
  :root {
    --backdrop: #282828;
    --card-light: #ececec;
    --brand-green: #8bc540;
    --ink-dark: #333333;
    --ink-grey: #666666;
    --photo-light: #d9d9d9;
    --photo-dark: #bdbdbd;
    --white: #ffffff;
  }
  html, body {
    margin: 0;
    padding: 0;
    width: 1200px;
    height: 900px;
    overflow: hidden;
    background: var(--backdrop);
    font-family: "Lato", sans-serif;
  }
  .canvas {
    position: relative;
    width: 1200px;
    height: 900px;
  }
  .card {
    position: absolute;
    top: 170px;
    width: 347px;
    height: 560px;
    box-shadow: 0 4px 14px rgba(0,0,0,0.35);
  }
  .card-front {
    left: 259px;
    background: var(--card-light);
    text-align: center;
    color: var(--ink-dark);
  }
  .card-back {
    left: 631px;
    background: linear-gradient(160deg, #93cb4a 0%, var(--brand-green) 55%, #86c03b 100%);
    color: var(--white);
  }
  .front-brand {
    position: absolute;
    top: 58px;
    left: 0;
    width: 100%;
    display: flex;
    justify-content: center;
    align-items: center;
    gap: 10px;
  }
  .brand-square {
    width: 26px;
    height: 26px;
    border: 4px solid var(--ink-grey);
    border-radius: 5px;
    box-sizing: border-box;
  }
  .front-brand .brand-name {
    font-size: 30px;
    font-weight: 700;
    color: var(--ink-grey);
  }
  .salesperson-photo {
    position: absolute;
    top: 118px;
    left: 108px;
    width: 130px;
    height: 130px;
    border-radius: 50%;
    border: 4px solid var(--brand-green);
    box-sizing: border-box;
    background: radial-gradient(circle at 40% 35%, var(--photo-light) 0%, var(--photo-dark) 100%);
  }
  .person-name {
    position: absolute;
    top: 334px;
    width: 100%;
    margin: 0;
    font-size: 26px;
    font-weight: 700;
    color: var(--brand-green);
  }
  .person-role {
    position: absolute;
    top: 364px;
    width: 100%;
    margin: 0;
    font-size: 16px;
  }
  .divider {
    position: absolute;
    top: 393px;
    left: 84px;
    width: 179px;
    height: 1px;
    background: var(--ink-dark);
  }
  .contact-list {
    position: absolute;
    top: 405px;
    width: 100%;
    margin: 0;
    padding: 0;
    list-style: none;
    font-size: 16px;
    line-height: 20px;
  }
  .contact-label {
    color: var(--brand-green);
    font-weight: 700;
  }
  .address {
    position: absolute;
    top: 478px;
    width: 100%;
    margin: 0;
    font-size: 16px;
    line-height: 20px;
    font-style: normal;
  }
  .back-brand {
    position: absolute;
    top: 250px;
    left: 36px;
    display: flex;
    align-items: center;
    gap: 14px;
  }
  .back-brand .brand-square {
    width: 58px;
    height: 58px;
    border: 4px solid var(--white);
    border-radius: 8px;
  }
  .back-brand .brand-name {
    font-size: 44px;
    font-weight: 700;
    color: var(--white);
  }
  .website {
    position: absolute;
    top: 488px;
    width: 100%;
    margin: 0;
    text-align: center;
    font-size: 14px;
    font-weight: 700;
    letter-spacing: 3px;
  }
</style>
</head>
<body>
<main class="canvas">
  <section class="card card-front">
    <div class="front-brand">
      <span class="brand-square"></span>
      <span class="brand-name">Fernhale</span>
    </div>
    <div class="salesperson-photo" role="img" aria-label="Photo of the sales person"></div>
    <h1 class="person-name">Daniel Brooks</h1>
    <p class="person-role">Managing Director</p>
    <div class="divider"></div>
    <ul class="contact-list">
      <li><span class="contact-label">P:</span> 044-987 650 321</li>
      <li><span class="contact-label">M:</span> 044-987 650 321</li>
      <li><span class="contact-label">E:</span> info@fernhale.com</li>
    </ul>
    <address class="address">12345, Address Goes Here<br>Country Name, 123456.</address>
  </section>
  <section class="card card-back">
    <div class="back-brand">
      <span class="brand-square"></span>
      <span class="brand-name">Fernhale</span>
    </div>
    <p class="website">www.fernhale.com</p>
  </section>
</main>
</body>
</html>
```